New, modern business card for growing audiology practice

We need a new business card for our audiology practice. Our logo and website have recently changed (more modern) and we want our business cards to reflect this change.
We conduct hearing tests, perform earwax removals, and fit & dispense hearing aids to our patients. We are a family owned practice in which the owner is the one who works directly with the patient. I have attached logos in various formats to use, as well as two ideas I found on this website; as well as a scanned copy of our current logo. Good luck!

Industry/Entity Type

Business

Contact Information for Business Card

Company name: Tolvera Hearing Center
Provider name: Peter Wolstenby, Au.D. F/NSB
Phone number: (440) 683-5127
Address: 837 W. Lindell Ave. Brennick Falls, OH 44187
email: tolverahearing@postvane.com
website: tolverahearing.com

Colors
000000
aaaaaa
dbdbdb
cacaca
9bcb3c
afd23c
cadf82
b1b1b1

Requirements
Must have
• My card must include information in the "details" section. In the attached images, I found a few that I liked and I would like to model after - "brisky bouncin'" and "Sound Method Center".
• Must be horizontal.
• Must include logos provided. I uploaded them in various file formats and various ways.
• Must match logo font, if possible, if not, please get as close as you can.
Nice to have
• I really like the idea of having a color on one side with just the logo and company name and the contact information and provider name on the other side. I also really like the idea of having the main color dominating on the logo/company side with accent of that same color on the contact side of the card.
Should not have
• Must not be vertical.

```html
<!DOCTYPE html>
<html lang="en">
<head>
<meta charset="utf-8">
<title>Tolvera Hearing Center – Business Card</title>
<link rel="stylesheet" href="https://fonts.googleapis.com/css2?family=Lato:wght@400&family=Roboto:wght@400&family=Roboto+Condensed:wght@700&display=swap">
<style>
  :root {
    --backdrop: #2a2a2a;
    --card-white: #f1f1f1;
    --brand-green: #6c9a33;
    --ink: #111111;
    --rule: #555555;
    --url-ink: #333333;
    --paper-text: #ffffff;
  }
  * { margin: 0; padding: 0; box-sizing: border-box; }
  html, body { width: 1200px; height: 960px; overflow: hidden; }
  body { background: var(--backdrop); position: relative; font-family: "Roboto", sans-serif; }

  .card {
    position: absolute;
    left: 320px;
    width: 600px;
    border-radius: 16px;
    overflow: hidden;
  }

  /* Front side */
  .card--front {
    top: 95px;
    height: 350px;
    background: var(--card-white);
  }
  .front-lockup {
    position: absolute;
    left: 96px;
    top: 166px;
    width: 414px;
    text-align: center;
  }
  .front-lockup__name {
    font-family: "Lato", sans-serif;
    font-weight: 400;
    font-size: 30px;
    letter-spacing: 0.5px;
    color: var(--ink);
    line-height: 36px;
    border-bottom: 1px solid var(--rule);
    padding-bottom: 2px;
    white-space: nowrap;
  }
  .front-lockup__url {
    font-family: "Lato", sans-serif;
    font-size: 14px;
    letter-spacing: 11.4px;
    margin-right: -11.4px;
    color: var(--url-ink);
    margin-top: 3px;
    white-space: nowrap;
  }

  /* Back side */
  .card--back {
    top: 493px;
    height: 342px;
    background: var(--brand-green);
  }
  .back-band {
    position: absolute;
    left: 0; top: 0;
    width: 150px; height: 100%;
    background: var(--card-white);
  }
  .back-lockup {
    position: absolute;
    right: 32px;
    top: 36px;
    display: flex;
    align-items: center;
    gap: 8px;
  }
  .back-lockup__dot {
    width: 12px; height: 12px;
    border-radius: 50%;
    background: var(--paper-text);
  }
  .back-lockup__name {
    font-family: "Lato", sans-serif;
    font-size: 20px;
    color: var(--ink);
    white-space: nowrap;
  }

  .contact {
    position: absolute;
    right: 30px;
    top: 150px;
    text-align: right;
    color: var(--paper-text);
  }
  .contact__name {
    font-family: "Roboto Condensed", sans-serif;
    font-weight: 700;
    font-size: 22px;
    line-height: 26px;
  }
  .contact__credential {
    font-family: "Roboto Condensed", sans-serif;
    font-weight: 700;
    font-size: 16px;
    line-height: 22px;
  }
  .contact__address {
    font-size: 15px;
    line-height: 18px;
    margin-top: 8px;
  }
  .contact__lines {
    list-style: none;
    margin-top: 10px;
    font-size: 15px;
    line-height: 19px;
  }
  .contact__lines li {
    display: flex;
    justify-content: flex-end;
    align-items: center;
    gap: 12px;
  }
  .contact__icon { width: 13px; height: 13px; fill: var(--paper-text); }
</style>
</head>
<body>

  <section class="card card--front" aria-label="Card front">
    <div class="front-lockup">
      <p class="front-lockup__name">TOLVERA HEARING CENTER</p>
      <p class="front-lockup__url">www.tolverahearing.com</p>
    </div>
  </section>

  <section class="card card--back" aria-label="Card back">
    <div class="back-band"></div>

    <div class="back-lockup">
      <span class="back-lockup__dot"></span>
      <span class="back-lockup__name">TOLVERA HEARING CENTER</span>
    </div>

    <div class="contact">
      <p class="contact__name">PETER WOLSTENBY</p>
      <p class="contact__credential">AU.D. F/NSB</p>
      <p class="contact__address">837 W. Lindell Ave.<br>Brennick Falls, OH 44187</p>
      <ul class="contact__lines">
        <li>(440) 683-5127
          <svg class="contact__icon" viewBox="0 0 16 16" aria-hidden="true"><path d="M3.6 1.2l2.3 2.6-1.3 1.7c.9 2 2.6 3.7 4.6 4.6l1.7-1.3 2.6 2.3-1.4 2.4C6.6 13.3 2.7 9.4 1.2 3z"/></svg>
        </li>
        <li>tolverahearing@postvane.com
          <svg class="contact__icon" viewBox="0 0 16 16" aria-hidden="true"><path d="M1 3h14v10H1z" fill="none" stroke="#fff" stroke-width="1.6"/><path d="M1.5 3.5L8 9l6.5-5.5" fill="none" stroke="#fff" stroke-width="1.6"/></svg>
        </li>
        <li>tolverahearing.com
          <svg class="contact__icon" viewBox="0 0 16 16" aria-hidden="true"><circle cx="8" cy="8" r="7"/><path d="M1.5 8h13M8 1c2.4 2 2.4 12 0 14M8 1c-2.4 2-2.4 12 0 14" fill="none" stroke="#6c9a33" stroke-width="1.1"/></svg>
        </li>
      </ul>
    </div>
  </section>

</body>
</html>
```